Business Card - high end, modern health care

Hey designers!

We need a double sided business card for the boutique, cutting edge physical therapy rehabilitation centre in Sydney's Northern Beaches.

With the most qualified physios in the area The Harbourview Motion Clinic does what other physiotherapy practices do not, we take our time with our patients giving them longer appointments, better physios and therefor faster results!

We guarantee that the service people receive at THMC will be unparalleled.

Hence we need a business card to reflect our modern, boutique, high end service. The final design needs to reflect that we are in a class of our own yet with the feel of beachside retreat.

Below I have attached our logo in both blue on white and white on blue. The exact colour is;
and the font that we have used in our logo is Tex Gyre Aventador.

I like the idea of the blue as the main colour as it is more eye catching and our signage onto the main road will be in this blue and in the interest of consistency across marketing the blue needs to be a part of the design. However I would appreciate a few designs onto a wooden background as this is a visual theme within the fitout of the practice.

The design needs to be of standard size (91x55mm).

Target Market(s)

We target people who have an end outcome in mind and those who have had poor experiences with other providers and ensure that everyone gets the care that they deserve with a premium service that is tailored to the individuals circumstances. As a premium service, the target market is highly educated, business and tech savvy with the additional target market of elderly people who have self funded their retirement and see value in paying for the best ongoing rehabilitation to maintain independence.

Industry/Entity Type

Physical Therapy

Contact Information for Business Card

Name, designation( Titled Musculoskeletal Physiotherapist... there will also be those in the company that have multiple designations ie 5 or 6 words long), phone number, email, facebook, instagram, address

Font styles to use
Sans Serif

Colors

Designer to choose colors to be used in the design.

Requirements
Must have
• Front - The logo as large as possible, blue or wooden theme, and all of the important details.
• Back - A blank space/lines on which to write appointment times (no "Appointment, date, time" etc.)
Nice to have
• facebook url
• logos for facebook and instagram
• Mini logos for the phone and email?

```html
<!DOCTYPE html>
<html lang="en">
<head>
<meta charset="utf-8">
<title>The Harbourview Motion Clinic – Business Card</title>
<link rel="stylesheet" href="https://fonts.googleapis.com/css2?family=Montserrat:wght@400;500;700&display=swap">
<style>
  :root {
    --brand-blue: #0b55a8;
    --brand-blue-deep: #084a94;
    --card-white: #ffffff;
    --rule-grey: #9aa0a6;
    --stage: #d9dcdf;
  }
  * { margin: 0; padding: 0; box-sizing: border-box; }
  html, body {
    width: 1200px; height: 900px; overflow: hidden;
    background: var(--stage);
    font-family: "Montserrat", sans-serif;
  }
  .canvas { position: relative; width: 1200px; height: 900px; }
  .card {
    position: absolute; left: 280px; width: 640px; height: 388px;
    border-radius: 18px; overflow: hidden;
    background: var(--card-white);
    box-shadow: 0 10px 30px rgba(0,0,0,.18);
  }
  .card--front { top: 48px; }
  .card--back  { top: 464px; }

  /* Front */
  .front-wave { position: absolute; inset: 0; width: 100%; height: 100%; }
  .brand {
    position: absolute; left: 40px; top: 36px;
    display: flex; align-items: center; gap: 16px;
    color: var(--brand-blue);
  }
  .brand__dot {
    width: 64px; height: 64px; border-radius: 50%;
    background: var(--brand-blue); flex: none;
  }
  .brand__name {
    font-weight: 700; font-size: 20px; line-height: 1.2;
    letter-spacing: 1px; text-transform: uppercase;
  }
  .contact {
    position: absolute; right: 36px; top: 250px;
    text-align: right; color: var(--card-white);
  }
  .contact__name {
    font-weight: 700; font-size: 22px; letter-spacing: .5px;
    text-transform: uppercase; line-height: 24px;
  }
  .contact__title { font-size: 14px; font-weight: 500; line-height: 17px; margin-bottom: 6px; }
  .contact__line {
    font-size: 12.5px; line-height: 16px;
    display: flex; justify-content: flex-end; align-items: center; gap: 7px;
  }
  .contact__line svg { width: 12px; height: 12px; flex: none; }

  /* Back */
  .back-band {
    position: absolute; left: 0; top: 0; width: 100%; height: 150px;
    background: var(--brand-blue);
    display: flex; align-items: center; justify-content: flex-end;
    padding-right: 40px; gap: 16px;
    color: var(--card-white);
  }
  .back-band .brand__dot { background: var(--card-white); width: 56px; height: 56px; }
  .back-band .brand__name { color: var(--card-white); font-size: 24px; }
  .write-lines {
    position: absolute; left: 40px; right: 40px; top: 150px; bottom: 0;
    display: flex; flex-direction: column; justify-content: space-evenly;
    padding: 10px 0;
  }
  .write-lines__rule { height: 1px; background: var(--rule-grey); }
</style>
</head>
<body>
<main class="canvas">

  <section class="card card--front" aria-label="Card front">
    <svg class="front-wave" viewBox="0 0 640 388" preserveAspectRatio="none" aria-hidden="true">
      <path d="M0,110 C150,215 320,244 440,240 C540,236 610,212 640,180 L640,388 L0,388 Z" fill="var(--brand-blue)"/>
      <path d="M0,84 C120,180 290,212 400,214 C290,222 140,206 0,104 Z" fill="var(--brand-blue)"/>
      <path d="M0,140 C130,222 290,242 420,242 C290,250 130,240 0,152 Z" fill="var(--card-white)"/>
      <path d="M430,226 C520,224 596,198 634,150 C606,204 530,234 430,232 Z" fill="var(--brand-blue-deep)"/>
    </svg>

    <div class="brand">
      <span class="brand__dot"></span>
      <div class="brand__name">The Harbourview<br>Motion Clinic</div>
    </div>

    <div class="contact">
      <div class="contact__name">Daniel Carter</div>
      <div class="contact__title">Director</div>
      <div class="contact__line">48 Ocean Parade, Suite 3,</div>
      <div class="contact__line">Harbour Town, PO 20871</div>
      <div class="contact__line">+61 2 5550 1824
        <svg viewBox="0 0 24 24" aria-hidden="true"><path fill="currentColor" d="M6.6 10.8a15 15 0 0 0 6.6 6.6l2.2-2.2c.3-.3.7-.4 1-.2 1.1.4 2.3.6 3.6.6.6 0 1 .4 1 1V20c0 .6-.4 1-1 1C10.6 21 3 13.4 3 4c0-.6.4-1 1-1h3.5c.6 0 1 .4 1 1 0 1.3.2 2.5.6 3.6.1.3 0 .7-.2 1z"/></svg>
      </div>
      <div class="contact__line">hello@harbourviewmotion.com
        <svg viewBox="0 0 24 24" aria-hidden="true"><rect x="3" y="5" width="18" height="14" rx="1.5" fill="none" stroke="currentColor" stroke-width="2"/><path d="M3.5 6l8.5 7 8.5-7" fill="none" stroke="currentColor" stroke-width="2"/></svg>
      </div>
      <div class="contact__line">www.harbourviewmotion.com
        <svg viewBox="0 0 24 24" aria-hidden="true"><circle cx="12" cy="12" r="9" fill="none" stroke="currentColor" stroke-width="2"/><path d="M3 12h18M12 3c3 3 3 15 0 18M12 3c-3 3-3 15 0 18" fill="none" stroke="currentColor" stroke-width="1.6"/></svg>
      </div>
    </div>
  </section>

  <section class="card card--back" aria-label="Card back">
    <div class="back-band">
      <span class="brand__dot"></span>
      <div class="brand__name">The Harbourview<br>Motion Clinic</div>
    </div>
    <div class="write-lines" aria-label="Space to write appointment times">
      <div class="write-lines__rule"></div>
      <div class="write-lines__rule"></div>
      <div class="write-lines__rule"></div>
      <div class="write-lines__rule"></div>
    </div>
  </section>

</main>
</body>
</html>
```